Marlowby Services Website Design

We have most content but require a professional design. We have a logo already and will need it utilized along with several of the photos from the attached documentation.
First page should have our mission and Vision and the synapsis provided in the word document. Visitors will be prompted to select from one of our 3 divisions from this page.
Each division will have the same list of tabs : About, Services, Safety, Careers and Contact.
Photos on each divisions page should be representative of the divisions offerings. The word doc attached contains the requested content and we are open to edits that would complement and fill the website.
I like the Quorvane site www.quorvane.example - they are our competition so cant be modeled directly after this.
Please include prompts to request quote at each service page. align the format of the geotechnical page to the other 2 divisions.
I used chat gpt for some of the content so will need it optimized for SCO.

```html
<!DOCTYPE html>
<html lang="en">
<head>
<meta charset="utf-8">
<title>Marlowby Services</title>
<link href="https://fonts.googleapis.com/css2?family=Audiowide&family=Lato:wght@400;700&family=Roboto+Condensed:wght@700&display=swap" rel="stylesheet">
<style>
:root{
  --red:#ec1c24;
  --ink:#111;
  --text:#333;
  --panel:#f3f3f3;
  --white:#fff;
  --footer:#121212;
  --rule:#3a3a3a;
}
*{margin:0;padding:0;box-sizing:border-box}
html,body{width:1200px;height:3367px;overflow:hidden}
body{position:relative;background:var(--white);font-family:'Lato',sans-serif;color:var(--text)}
.abs{position:absolute}
.display{font-family:'Audiowide',sans-serif}
.btn{position:absolute;background:var(--red);color:var(--white);font-size:14px;display:flex;align-items:center;justify-content:center;text-decoration:none}

/* header */
.site-header{position:absolute;left:0;top:0;width:1200px;height:60px;background:var(--white)}
.brand{position:absolute;font-family:'Audiowide',sans-serif;color:var(--red);letter-spacing:2px}
.site-header .brand{left:141px;top:8px;font-size:36px;line-height:44px}
.main-nav a{position:absolute;top:21px;font-size:13px;color:var(--ink);text-decoration:none}

/* hero */
.hero{position:absolute;left:0;top:60px;width:1200px;height:550px;
  background:linear-gradient(180deg,#1d3f9c 0%,#3a4f9a 25%,#c9552f 52%,#f08a1c 60%,#1b2a55 68%,#24406e 100%)}
.hero-kicker{position:absolute;left:142px;top:214px;color:var(--white);font-size:15px}
.hero-title{position:absolute;left:142px;top:240px;color:var(--white);font-family:'Roboto Condensed',sans-serif;font-weight:700;font-size:36px;line-height:47px}

/* services */
.section-title{position:absolute;left:0;width:1200px;text-align:center;font-family:'Audiowide',sans-serif;color:var(--red);font-size:34px;letter-spacing:1px}
.section-sub{position:absolute;left:0;width:1200px;text-align:center;font-size:15px;color:var(--ink)}
.service-card{position:absolute;width:297px;height:297px;background:var(--panel);text-align:center}
.service-card svg{position:absolute;left:108px;top:40px}
.service-card h3{position:absolute;left:0;right:0;font-family:'Audiowide',sans-serif;font-weight:400;font-size:16px;color:var(--ink);line-height:18px}
.service-card p{position:absolute;left:30px;right:30px;font-size:12px;line-height:20.5px;color:var(--text)}

/* vision */
.vision-panel{position:absolute;left:427px;top:1583px;width:773px;height:545px;background:var(--panel)}
.accent-block{position:absolute;background:var(--red)}
.photo{position:absolute}
.statement h2{position:absolute;font-family:'Audiowide',sans-serif;font-weight:400;font-size:27px;color:#2a2a2a}
.statement p{position:absolute;left:599px;width:450px;font-size:12px;line-height:21.6px;color:var(--text)}

/* divisions */
.division{position:absolute;top:2306px;width:282px;height:313px;color:var(--white)}
.division h3{position:absolute;left:18px;font-family:'Audiowide',sans-serif;font-weight:400;font-size:15px;line-height:18px}
.division p{position:absolute;left:19px;width:245px;font-size:11px;line-height:20px}
.arrow{position:absolute;width:20px;height:20px;border-radius:50%;background:var(--red);right:14px;bottom:20px;display:flex;align-items:center;justify-content:center}

.tagline{position:absolute;left:0;top:2714px;width:1200px;text-align:center;font-size:24px;line-height:32px;color:var(--ink);font-weight:700}
.tagline .display{color:var(--red);font-weight:400}

/* footer */
.site-footer{position:absolute;left:0;top:2951px;width:1200px;height:416px;background:var(--footer);color:var(--white)}
.site-footer .brand{left:0;width:1200px;text-align:center;top:76px;font-size:36px}
.rule{position:absolute;left:141px;width:920px;height:1px;background:var(--rule)}
.foot-nav a{position:absolute;top:196px;font-size:13px;color:var(--white);text-decoration:none;transform:translateX(-50%)}
.contact{position:absolute;top:290px;display:flex;gap:8px;font-size:12px;line-height:20px}
.contact .ico{width:30px;height:30px;border:1px solid #ddd;border-radius:50%;display:flex;align-items:center;justify-content:center;flex:none;margin-top:3px}
.contact b{font-family:'Audiowide',sans-serif;font-weight:400;font-size:13px}
.copyright{position:absolute;left:0;width:1200px;top:378px;text-align:center;font-size:11px}
</style>
</head>
<body>

<header class="site-header">
  <div class="brand">MARLOWBY</div>
  <nav class="main-nav">
    <a style="left:644px">About</a>
    <a style="left:716px">Services</a>
    <a style="left:801px">Safety</a>
    <a style="left:874px">Careers</a>
  </nav>
  <a class="btn" style="left:942px;top:13px;width:118px;height:34px">Contact Us</a>
</header>

<section class="hero" role="img" aria-label="Oil pumpjacks silhouetted against a sunset above a field of solar panels">
  <p class="hero-kicker">Delivering safe, reliable aerial access and maintenance services to</p>
  <h1 class="hero-title">Oil &amp; Gas,Construction, Utility, &amp;<br>Renewable energy Sector</h1>
  <a class="btn" style="left:141px;top:339px;width:116px;height:32px">Contact Us</a>
</section>

<section class="services">
  <h2 class="section-title" style="top:676px">OUR SERVICES</h2>
  <p class="section-sub" style="top:730px">Delivering safe, reliable aerial access and maintenance services</p>

  <article class="service-card" style="left:141px;top:927px">
    <svg width="84" height="84" viewBox="0 0 84 84" fill="none" stroke="#ec1c24" stroke-width="2.4"><circle cx="62" cy="18" r="6"/><path d="M62 4v5M62 27v5M48 18h5M71 18h5M52 8l3 3M69 25l3 3M72 8l-3 3M55 25l-3 3"/><rect x="38" y="48" width="36" height="22"/><path d="M44 48v22M50 48v22M56 48v22M62 48v22M68 48v22M56 70v10M46 80h20M16 80V30M16 42c-10-4-10-16 0-20 10 4 10 16 0 20zM16 56c10-10 20-8 22 0"/></svg>
    <h3 style="top:136px">Renewable energy<br>industries</h3>
    <p style="top:196px">Lorem ipsum dolor sit amet, consectetur adipiscing elit, sed do eiusmod tempor incididunt ut labore et dolore magna aliqua dolore magna sit</p>
  </article>

  <article class="service-card" style="left:453px;top:771px">
    <svg width="84" height="84" viewBox="0 0 84 84" fill="none" stroke="#ec1c24" stroke-width="2.4"><path d="M6 80h72M12 80V40h20v40M18 40V6h8v34M40 80V20h14v60M60 80V50c0-6 12-6 12 0v30M22 60a6 6 0 1 0 0.1 0M54 30h10v14"/></svg>
    <h3 style="top:146px">Oil&amp;Gas</h3>
    <p style="top:176px">Lorem ipsum dolor sit amet, consectetur adipiscing elit, sed do eiusmod tempor incididunt ut labore et dolore magna aliqua dolore magna sit</p>
  </article>

  <article class="service-card" style="left:453px;top:1081px">
    <svg width="84" height="84" viewBox="0 0 84 84" fill="none" stroke="#ec1c24" stroke-width="2.4"><path d="M4 80h76M30 80l12-56 12 56M35 56h14M33 68h18M8 10l60 10M42 14v10M66 18l4 14M12 60a6 6 0 1 0 0.1 0M14 80V66"/></svg>
    <h3 style="top:152px">Construction</h3>
    <p style="top:186px">Lorem ipsum dolor sit amet, consectetur adipiscing elit, sed do eiusmod tempor incididunt ut labore et dolore magna aliqua dolore magna sit</p>
  </article>

  <article class="service-card" style="left:765px;top:927px">
    <svg width="84" height="84" viewBox="0 0 84 84" fill="none" stroke="#ec1c24" stroke-width="2.4" style="top:40px"><path d="M42 4l6 6 8-2 3 8 8 3-2 8 6 6-6 6 2 8-8 3-3 8-8-2-6 6-6-6-8 2-3-8-8-3 2-8-6-6 6-6-2-8 8-3 3-8 8 2z"/><circle cx="42" cy="42" r="20"/><path d="M34 30v26M50 30l-10 24M44 36l10 4"/></svg>
    <h3 style="top:143px">Utility</h3>
    <p style="top:178px">Lorem ipsum dolor sit amet, consectetur adipiscing elit, sed do eiusmod tempor incididunt ut labore et dolore magna aliqua dolore magna sit</p>
  </article>
</section>

<section class="statement">
  <div class="vision-panel"></div>
  <div class="accent-block" style="left:440px;top:1472px;width:131px;height:128px"></div>
  <div class="photo" style="left:0;top:1490px;width:554px;height:573px;background:linear-gradient(160deg,#39472f 0%,#5a6a4a 35%,#d7d9d6 55%,#8a8f88 80%,#5e5e58 100%)" role="img" aria-label="Company aerial lift truck parked in a forest yard"></div>

  <svg class="abs" style="left:596px;top:1660px" width="38" height="38" viewBox="0 0 38 38" fill="none" stroke="#ec1c24" stroke-width="1.8"><path d="M3 19c8-10 24-10 32 0-8 10-24 10-32 0z"/><circle cx="19" cy="19" r="5"/><path d="M19 2v5M19 31v5M6 7l3 3M32 7l-3 3"/></svg>
  <h2 style="left:654px;top:1656px">Our Vision</h2>
  <p style="top:1723px">To be the leading provider of aerial access, geotechnical drilling, and service solutions, setting the standard for excellence in safety, efficiency, and environmental stewardship.</p>

  <svg class="abs" style="left:596px;top:1824px" width="40" height="40" viewBox="0 0 40 40" fill="none" stroke="#ec1c24" stroke-width="1.8"><circle cx="19" cy="21" r="17"/><circle cx="19" cy="21" r="11"/><circle cx="19" cy="21" r="5"/><path d="M19 21L35 5M30 4v6h6"/></svg>
  <h2 style="left:654px;top:1822px">Our Mission</h2>
  <p style="top:1886px">At Marlowby, our mission is to deliver unparalleled aerial access, geotechnical drilling, and service and maintenance solutions, consistently exceeding our clients' expectations. We strive to achieve this by investing in cutting-edge technology, fostering a culture of safety and continuous improvement, and prioritizing environmental sustainability. Through collaboration, integrity, and dedication, we aim to contribute to the success of our clients while maintaining the highest standards of quality and professionalism.</p>
</section>

<section class="divisions">
  <h2 class="section-title" style="top:2208px">OUR DIVISIONS</h2>
  <div class="accent-block" style="left:319px;top:2290px;width:120px;height:119px"></div>

  <article class="division" style="left:141px;background:linear-gradient(180deg,#2e3c5c 0%,#3b4660 55%,#5a4a44 100%)" role="img" aria-label="Aerial lift beside a wind turbine tower at dusk">
    <h3 style="top:166px">Aerial Access</h3>
    <p style="top:190px">Marlowby is a full-service wind energy service provider specializing in blade access &amp; repair , service and maintenance , &amp; trouble shooting on most wind turbine platforms.</p>
    <span class="arrow"><svg width="10" height="10" viewBox="0 0 10 10" fill="none" stroke="#fff" stroke-width="1.5"><path d="M1 5h8M6 2l3 3-3 3"/></svg></span>
  </article>

  <article class="division" style="left:459px;background:linear-gradient(180deg,#1f3a34 0%,#2f4a3a 45%,#5a2a2a 70%,#1a2420 100%)" role="img" aria-label="Red tracked geotechnical drill rig in a forest clearing">
    <h3 style="top:274px">Geotechnical Drilling</h3>
    <span class="arrow"><svg width="10" height="10" viewBox="0 0 10 10" fill="none" stroke="#fff" stroke-width="1.5"><path d="M1 5h8M6 2l3 3-3 3"/></svg></span>
  </article>

  <article class="division" style="left:779px;background:linear-gradient(200deg,#9fb6d6 0%,#3d63a8 40%,#1e3f86 100%)" role="img" aria-label="Wind turbine against a deep blue sky">
    <h3 style="top:264px">Renewable Energy<br>Services</h3>
    <span class="arrow"><svg width="10" height="10" viewBox="0 0 10 10" fill="none" stroke="#fff" stroke-width="1.5"><path d="M1 5h8M6 2l3 3-3 3"/></svg></span>
  </article>
</section>

<p class="tagline"><span class="display">MARLOWBY</span> Is A Full-service Wind Energy Service Provider<br>Specializing In Blade Access And Repair, Service And Maintenance,<br>And Trouble Shooting On Most Wind Turbine Platforms.</p>
<a class="btn" style="left:541px;top:2826px;width:116px;height:34px">Contact Us</a>
<div class="abs" style="left:877px;top:2860px;width:81px;height:91px;background:var(--panel)"></div>
<div class="accent-block" style="left:979px;top:2860px;width:81px;height:91px"></div>

<footer class="site-footer">
  <div class="brand">MARLOWBY</div>
  <div class="rule" style="top:157px"></div>
  <nav class="foot-nav">
    <a style="left:339px">Home</a>
    <a style="left:430px">About</a>
    <a style="left:529px">Services</a>
    <a style="left:629px">Safety</a>
    <a style="left:727px">Careers</a>
    <a style="left:841px;font-size:14px">Contact Us</a>
  </nav>
  <div class="rule" style="top:250px"></div>

  <div class="contact" style="left:198px">
    <span class="ico"><svg width="12" height="16" viewBox="0 0 12 16" fill="none" stroke="#fff" stroke-width="1.5"><path d="M6 15S1 9 1 6a5 5 0 0 1 10 0c0 3-5 9-5 9z"/><circle cx="6" cy="6" r="1.8"/></svg></span>
    <div>88 Ridgeline Road Harrow Flats<br>AB T0X-1B0</div>
  </div>
  <div class="contact" style="left:525px">
    <span class="ico"><svg width="14" height="14" viewBox="0 0 14 14" fill="none" stroke="#fff" stroke-width="1.5"><path d="M3 1l2 3-1.5 1.5a8 8 0 0 0 5 5L10 9l3 2-1 2C6 13 1 8 1 2z"/></svg></span>
    <div><b>Phone</b><br>(555)-014-2290</div>
  </div>
  <div class="contact" style="left:791px">
    <span class="ico"><svg width="14" height="10" viewBox="0 0 14 10" fill="none" stroke="#fff" stroke-width="1.5"><rect x="1" y="1" width="12" height="8"/><path d="M1 1l6 5 6-5"/></svg></span>
    <div><b>Email</b><br>career@marlowbyservices.example</div>
  </div>

  <div class="rule" style="top:353px"></div>
  <p class="copyright">© 2024 <b>MARLOWBY</b>. All Rights Reserved.</p>
</footer>

</body>
</html>
```